business card deign

Logo needs the following on it.
1. attached logo
2. Tagline - "If it keeps the cooler full or the night rolling...we're on it!"
3. Name- Dalton Pikes, Founder and CPO
4. Address - 412 E. Carver Avenue, Ste 2207, Tampa, FL. 33917
5. Phone - 555.318.4726

```html
<!DOCTYPE html>
<html lang="en">
<head>
<meta charset="utf-8">
<title>Wallaro Business Card</title>
<link href="https://fonts.googleapis.com/css2?family=Montserrat:wght@400;500;700&display=swap" rel="stylesheet">
<style>
  :root {
    --backdrop: #b4b4b4;
    --card: #1d1d1d;
    --card-deep: #141414;
    --ink: #ffffff;
    --ink-soft: #d8d8d8;
    --rule: #8a8a8a;
  }
  * { margin: 0; padding: 0; box-sizing: border-box; }
  html, body {
    width: 1200px; height: 900px; overflow: hidden;
    background: var(--backdrop);
    font-family: "Montserrat", sans-serif;
  }
  .stage {
    position: relative; width: 1200px; height: 900px;
    display: flex; flex-direction: column; align-items: center; justify-content: center; gap: 40px;
  }
  .card {
    position: relative; width: 700px; height: 400px;
    border-radius: 22px; background: var(--card); overflow: hidden;
    box-shadow: 0 10px 30px rgba(0,0,0,.28);
  }
  /* Front */
  .brand {
    position: absolute; left: 60px; top: 190px; width: 240px;
    display: flex; align-items: center; gap: 12px;
  }
  .brand-dot { width: 22px; height: 22px; border-radius: 50%; background: var(--ink); flex: none; }
  .brand-name {
    color: var(--ink); font-weight: 700; font-size: 28px; letter-spacing: 3px; white-space: nowrap;
  }
  .divider {
    position: absolute; left: 330px; top: 40px; width: 1px; height: 230px; background: var(--rule);
  }
  .contact { position: absolute; left: 356px; top: 40px; right: 30px; color: var(--ink-soft); }
  .person-name { color: var(--ink); font-weight: 700; font-size: 22px; line-height: 1.1; }
  .person-role { font-size: 13px; margin-top: 4px; }
  .address { font-size: 13px; line-height: 1.35; margin-top: 16px; }
  .lines { list-style: none; margin-top: 12px; }
  .lines li { display: flex; align-items: center; gap: 10px; font-size: 13px; line-height: 1; margin-bottom: 11px; }
  .lines svg { width: 13px; height: 13px; fill: var(--ink); flex: none; }
  .tagline {
    position: absolute; left: 250px; right: 30px; bottom: 48px;
    color: var(--ink-soft); font-size: 13px; white-space: nowrap;
  }
  /* Back */
  .pattern-field {
    position: absolute; inset: 0;
    background: radial-gradient(ellipse at 15% 80%, #3a3a3a 0%, var(--card) 45%, var(--card-deep) 100%);
  }
  .back-mark {
    position: absolute; left: 470px; top: 235px;
    display: flex; align-items: center; gap: 8px;
  }
  .back-mark .brand-dot { width: 12px; height: 12px; }
  .back-mark .brand-name { font-size: 16px; letter-spacing: 2px; }
</style>
</head>
<body>
<main class="stage">
  <section class="card card-front">
    <div class="brand">
      <span class="brand-dot"></span>
      <span class="brand-name">WALLARO</span>
    </div>
    <div class="divider"></div>
    <div class="contact">
      <h1 class="person-name">Dalton Pikes</h1>
      <p class="person-role">Founder and CPO</p>
      <p class="address">412 E. Carver Avenue, Ste 2207,<br>Tampa, FL. 33917</p>
      <ul class="lines">
        <li>
          <svg viewBox="0 0 24 24" aria-hidden="true"><path d="M6.6 10.8a15 15 0 0 0 6.6 6.6l2.2-2.2a1 1 0 0 1 1-.25 11.4 11.4 0 0 0 3.6.57 1 1 0 0 1 1 1V20a1 1 0 0 1-1 1A17 17 0 0 1 3 4a1 1 0 0 1 1-1h3.5a1 1 0 0 1 1 1c0 1.25.2 2.45.57 3.6a1 1 0 0 1-.25 1z"/></svg>
          555.318.4726
        </li>
        <li>
          <svg viewBox="0 0 24 24" aria-hidden="true"><path d="M2 5h20v14H2z M3 6l9 7 9-7" fill="none" stroke="#fff" stroke-width="2"/></svg>
          info@wallaro.com
        </li>
        <li>
          <svg viewBox="0 0 24 24" aria-hidden="true"><circle cx="12" cy="12" r="9" fill="none" stroke="#fff" stroke-width="2"/><path d="M3 12h18M12 3c3 3 3 15 0 18M12 3c-3 3-3 15 0 18" fill="none" stroke="#fff" stroke-width="1.6"/></svg>
          www.wallaro.com
        </li>
      </ul>
    </div>
    <p class="tagline">If it keeps the cooler full or the night rolling...we're on it</p>
  </section>

  <section class="card card-back">
    <div class="pattern-field" role="img" aria-label="Repeating tone-on-tone brand mark pattern in dark grey on black"></div>
    <div class="back-mark">
      <span class="brand-dot"></span>
      <span class="brand-name">WALLARO</span>
    </div>
  </section>
</main>
</body>
</html>
```